Small Business Consulting Firm Needs Letterhead

We need a letterhead for our company "Brightpath Plus". Our company does outbound calling and mailing to business owner's companies who have taken high interest loans. These loans tend to put these businesses in a big financial bind short term, and we help them find better financial options. We would like the design to match our colors of our logo. Headers and footers would look nice, but we are open. We would want it to include our address, website, phone, and email info. Our address - 2000 E. Lamar Blvd. Suite 600Website - www.safeguardtoday.comEmail - info@safeguardtoday.comPhone - 855-726-1938
Industry/Entity Type
Financial Planning
Look and feel
Each slider illustrates characteristics of the customer's brand and the style your logo design should communicate.

```html
<!DOCTYPE html>
<html lang="en">
<head>
<meta charset="utf-8">
<title>Brightpath Plus Letterhead</title>
<link href="https://fonts.googleapis.com/css2?family=Montserrat:wght@300;400;500&display=swap" rel="stylesheet">
<style>
  :root {
    --backdrop: #dbe8ee;
    --paper: #ffffff;
    --green: #8cc63f;
    --green-deep: #74ad3a;
    --blue: #2fa7d9;
    --ink: #5a5a5a;
    --ink-strong: #3f3f3f;
  }
  * { margin: 0; padding: 0; box-sizing: border-box; }
  html, body {
    width: 1200px; height: 860px; overflow: hidden;
    background: var(--backdrop);
    font-family: "Montserrat", Arial, sans-serif;
    color: var(--ink);
  }
  .letterhead {
    position: absolute; left: 302px; top: 9px;
    width: 596px; height: 842px;
    background: var(--paper);
    box-shadow: 0 6px 22px rgba(40, 70, 90, 0.18);
    overflow: hidden;
  }
  .side-band {
    position: absolute; left: 0; top: 0; bottom: 0; width: 34px;
    background: linear-gradient(180deg, var(--green) 0%, #9ccf55 45%, var(--green-deep) 100%);
  }
  .brand {
    position: absolute; top: 78px; left: 300px;
    display: flex; align-items: center; gap: 10px;
  }
  .brand-square { width: 14px; height: 14px; background: var(--green); }
  .brand-name {
    font-weight: 400; font-size: 21px; letter-spacing: 2.5px;
    text-transform: uppercase; color: var(--ink);
  }
  .letter {
    position: absolute; left: 92px; right: 56px; top: 150px;
    font-size: 10.5px; line-height: 1.65; font-weight: 400;
    letter-spacing: 0.4px;
  }
  .letter p { margin-bottom: 14px; }
  .date { margin-bottom: 16px; }
  .recipient { margin-left: 14px; margin-bottom: 20px; }
  .salutation { margin-left: 6px; }
  .body-text { text-align: justify; margin-bottom: 4px !important; }
  .closing { margin-top: 26px; }
  .signatory { margin-top: 18px; }
  .signatory .name { font-size: 13px; font-weight: 500; color: var(--ink-strong); letter-spacing: 0.6px; }
  .signatory .role { letter-spacing: 3px; }
  .contact {
    position: absolute; bottom: 46px;
    font-size: 10px; line-height: 1.9; letter-spacing: 0.4px;
  }
  .contact-left { left: 70px; }
  .contact-right { left: 330px; }
  .contact-line { display: flex; align-items: center; gap: 7px; }
  .contact-line svg { width: 9px; height: 9px; flex: none; }
</style>
</head>
<body>
  <main class="letterhead">
    <div class="side-band"></div>

    <header class="brand">
      <span class="brand-square"></span>
      <span class="brand-name">Brightpath Plus</span>
    </header>

    <section class="letter">
      <p class="date">Date: 20 November 2018</p>
      <p class="recipient">To<br>Millbrook Orchard Ltd.<br>48 Fernhill Road, Suite# B<br>Leeds, UK LS2 7HQ</p>
      <p class="salutation">Dear Holloway,</p>
      <p class="body-text">Lorem Ipsum is simply dummy text of the printing and typesetting industry. Lorem Ipsum has been the industry’s standard dummy text ever since the 1500s, when an unknown printer took a galley of type and scrambled it to make a type specimen book. It has survived not only five centuries, but also the leap into electronic type-setting, remaining essentially unchanged. It was popularised in the 1960s with the release of Typeline sheets containing Lorem Ipsum passages, and more recently with desktop publishing software like Pagecraft Studio including versions of Lorem Ipsum.</p>
      <p class="body-text">Lorem Ipsum is simply dummy text of the printing and typesetting industry. Lorem Ipsum has been the industry’s.</p>
      <p class="closing">Thanking you</p>
      <div class="signatory">
        <div class="name">Daniel Reeve Marsh</div>
        <div class="role">CEO</div>
      </div>
    </section>

    <footer>
      <div class="contact contact-left">
        <div class="contact-line">
          <svg viewBox="0 0 10 10" aria-hidden="true"><path d="M5 0a3.5 3.5 0 0 0-3.5 3.5C1.5 6 5 10 5 10s3.5-4 3.5-6.5A3.5 3.5 0 0 0 5 0zm0 5a1.5 1.5 0 1 1 0-3 1.5 1.5 0 0 1 0 3z" fill="#8cc63f"/></svg>
          <span>4170 W. Corwin Ave. Suite 310</span>
        </div>
        <div class="contact-line">
          <svg viewBox="0 0 10 10" aria-hidden="true"><path d="M2 0.5 3.8 2.6 2.8 4a6 6 0 0 0 3.2 3.2l1.4-1L9.5 8 8.3 9.5C4 9.3 0.7 6 0.5 1.7z" fill="#8cc63f"/></svg>
          <span>855-726-1938</span>
        </div>
      </div>
      <div class="contact contact-right">
        <div class="contact-line">
          <svg viewBox="0 0 10 10" aria-hidden="true"><rect x="0.5" y="2" width="9" height="6" fill="#2fa7d9"/><path d="M0.5 2 5 5.5 9.5 2" stroke="#fff" stroke-width="0.9" fill="none"/></svg>
          <span>info@brightpathplus.com</span>
        </div>
        <div class="contact-line">
          <svg viewBox="0 0 10 10" aria-hidden="true"><circle cx="5" cy="5" r="4.5" fill="#2fa7d9"/></svg>
          <span>www.brightpathplus.com</span>
        </div>
      </div>
    </footer>
  </main>
</body>
</html>
```